Coastline Premier Retreats Business Card Design

Design a business card for Coastline Premier Retreats. Look at the website for colors and reference. Card should have logo, name, title, office number, mobile number, email, URL and a tagline like, "Luxury Hotel & Resort Email Marketing" (This might change).

https://www.coastlinepremierretreats.example

The rest I will leave up to your imagination.

Contact Information for Business Card

Logo, name, title, office number, mobile number, email, URL and a tagline like, "Luxury Hotel & Resort Email Marketing" (This might change).

```html
<!DOCTYPE html>
<html lang="en">
<head>
<meta charset="utf-8">
<title>Coastline Premier Retreats – Business Card</title>
<link href="https://fonts.googleapis.com/css2?family=Open+Sans:wght@400;600;700&display=swap" rel="stylesheet">
<style>
  :root {
    --bg: #e2e3e5;
    --card: #1f1f23;
    --orange: #f07522;
    --white: #ffffff;
    --muted: #e9e9ea;
  }
  * { box-sizing: border-box; margin: 0; padding: 0; }
  html, body { width: 1200px; height: 780px; overflow: hidden; }
  body {
    background: var(--bg);
    font-family: "Open Sans", Arial, sans-serif;
    position: relative;
  }
  .card {
    position: absolute;
    top: 240px;
    width: 520px;
    height: 300px;
    background: var(--card);
    overflow: hidden;
  }
  .card--front { left: 50px; }
  .card--back { left: 630px; }

  /* Front */
  .tagline-band {
    position: absolute;
    left: 0; top: 0;
    width: 96px; height: 100%;
    background: var(--orange);
  }
  .tagline {
    position: absolute;
    left: 48px; top: 150px;
    width: 260px;
    transform: translate(-50%, -50%) rotate(-90deg);
    color: var(--white);
    font-size: 15px;
    line-height: 1.35;
    text-align: center;
  }
  .front-logo {
    position: absolute;
    right: 34px; top: 30px;
    color: var(--white);
    font-weight: 700;
    font-size: 20px;
    letter-spacing: 1px;
    text-transform: uppercase;
  }
  .name-tab {
    position: absolute;
    right: 0; top: 92px;
    width: 14px; height: 40px;
    background: var(--orange);
  }
  .person {
    position: absolute;
    right: 34px; top: 90px;
    text-align: right;
  }
  .person__name {
    font-size: 26px;
    font-weight: 700;
    color: var(--white);
    line-height: 1.1;
  }
  .person__first { color: var(--orange); }
  .person__title {
    font-size: 14px;
    color: var(--muted);
    margin-top: 4px;
  }
  .contacts {
    position: absolute;
    right: 34px; top: 178px;
    list-style: none;
    text-align: right;
  }
  .contacts li {
    display: flex;
    justify-content: flex-end;
    align-items: center;
    gap: 8px;
    color: var(--muted);
    font-size: 13px;
    line-height: 23px;
  }
  .contacts svg { width: 13px; height: 13px; flex: none; }

  /* Back */
  .back-logo {
    position: absolute;
    inset: 0;
    display: flex;
    flex-direction: column;
    align-items: center;
    justify-content: center;
    color: var(--white);
    font-weight: 700;
    font-size: 30px;
    letter-spacing: 2px;
    line-height: 1.25;
    text-transform: uppercase;
    text-align: center;
  }
</style>
</head>
<body>
  <section class="card card--front" aria-label="Business card front">
    <div class="tagline-band">
      <p class="tagline">Luxury Hotel &amp;<br>Resort Email Marketing</p>
    </div>
    <div class="front-logo">Coastline Premier Retreats</div>
    <div class="name-tab"></div>
    <div class="person">
      <p class="person__name"><span class="person__first">Marina</span> Voskova</p>
      <p class="person__title">Co-Founder</p>
    </div>
    <ul class="contacts">
      <li>(555) 014-2758
        <svg viewBox="0 0 16 16" aria-hidden="true"><path fill="#f07522" d="M3.5 1h3l1 3.5-2 1.2a9 9 0 0 0 4.8 4.8l1.2-2 3.5 1v3a1.5 1.5 0 0 1-1.5 1.5A13 13 0 0 1 2 2.5 1.5 1.5 0 0 1 3.5 1z"/></svg>
      </li>
      <li>(555) 014-7777
        <svg viewBox="0 0 16 16" aria-hidden="true"><rect x="4" y="1" width="8" height="14" rx="1.5" fill="none" stroke="#f07522" stroke-width="1.6"/><circle cx="8" cy="12.5" r="0.9" fill="#f07522"/></svg>
      </li>
      <li>www.coastlinepremierretreats.example
        <svg viewBox="0 0 16 16" aria-hidden="true"><circle cx="8" cy="8" r="6.5" fill="none" stroke="#f07522" stroke-width="1.5"/><path d="M1.5 8h13M8 1.5c-2.5 3-2.5 10 0 13M8 1.5c2.5 3 2.5 10 0 13" fill="none" stroke="#f07522" stroke-width="1.2"/></svg>
      </li>
      <li>info@coastlinepremierretreats.example
        <svg viewBox="0 0 16 16" aria-hidden="true"><rect x="1" y="3" width="14" height="10" rx="1" fill="#f07522"/><path d="M1.5 3.8 8 9l6.5-5.2" fill="none" stroke="#1f1f23" stroke-width="1.3"/></svg>
      </li>
    </ul>
  </section>

  <section class="card card--back" aria-label="Business card back">
    <div class="back-logo">
      <span>Coastline</span>
      <span>Premier Retreats</span>
    </div>
  </section>
</body>
</html>
```